Kelp Row Arc need a business card designed

Descriptions:

Kelp Row Arc is a recruiting firm that only recruits sales people. Our advantage In the market is that we use A.I. software to recruit and pre assess candidates to find the top 20% of talent.

Here is the copy needed on each side of the card

Side #1.

Photo/Headshot
THOMAS MERROW
CEO
555-318-4427
www.KelpRowArc.example
tmerrow@KelpRowArc.example
Marlow Bend, ST

"Finding & Hiring Sales People Sucks!"
"Using the power of A.I. assessment tools to find you the top 20% of sales talent guaranteed!"

Side 2.

"The True cost of a bad hire can be as high as 10 X the first year salary"

"With KELP ROW ARC:
50% Faster time to hire
83% New Hire retention
96% Of wrong hires eliminated
50% Lower sales turnover

Link to ZIP guidelines / Templates for PhotoShop, InDesgin & Illustrator:
https://www.filevaultly.example/scl/fo/qpzt7yrnwke2lsa4cdjbv/h?rlkey=tnw83kfpqzr1c5vyxlbe2ad9&dl=0

```html
<!DOCTYPE html>
<html lang="en">
<head>
<meta charset="utf-8">
<title>Kelp Row Arc — Business Card</title>
<link href="https://fonts.googleapis.com/css2?family=Montserrat:wght@400;500;600;700;800&display=swap" rel="stylesheet">
<style>
  :root {
    --navy: #0a2f7d;
    --sky: #0f9be0;
    --white: #ffffff;
    --ink: #111827;
    --backdrop: #e9eaec;
  }
  * { box-sizing: border-box; margin: 0; padding: 0; }
  html, body { width: 1200px; height: 856px; overflow: hidden; }
  body {
    background: var(--backdrop);
    font-family: "Montserrat", sans-serif;
    position: relative;
  }
  .card {
    position: absolute;
    top: 273px;
    width: 540px;
    height: 310px;
    overflow: hidden;
    box-shadow: 0 8px 24px rgba(0,0,0,.18);
  }
  .card--front { left: 40px; background: var(--white); }
  .card--back { left: 620px; background: var(--navy); color: var(--white); }

  .card__shapes { position: absolute; inset: 0; }

  .brand {
    position: absolute;
    display: flex;
    align-items: center;
    gap: 8px;
    font-weight: 600;
    letter-spacing: .5px;
  }
  .brand__square { width: 12px; height: 12px; background: var(--sky); }
  .brand--front { left: 24px; top: 26px; font-size: 21px; color: var(--navy); }

  .headline {
    position: absolute;
    right: 22px; top: 22px;
    width: 300px;
    text-align: right;
    font-size: 11.5px;
    font-weight: 500;
    line-height: 1.45;
    color: var(--ink);
  }

  .identity { position: absolute; left: 28px; top: 122px; color: var(--white); }
  .identity__name { font-size: 25px; font-weight: 800; letter-spacing: .5px; line-height: 1.1; }
  .identity__role { font-size: 13px; font-weight: 400; margin-top: 2px; }

  .contact {
    position: absolute; left: 36px; top: 192px;
    list-style: none;
    font-size: 13px; font-weight: 500; color: var(--ink);
  }
  .contact__item { display: flex; align-items: center; gap: 10px; height: 22px; }
  .contact__icon { width: 14px; height: 14px; fill: var(--navy); flex: none; }
  .contact__item--plain { padding-left: 24px; }

  .headshot {
    position: absolute; left: 362px; top: 92px;
    width: 160px; height: 152px;
    background: linear-gradient(160deg, #c9b5a6 0%, #3a4560 55%, #1f2a44 100%);
    clip-path: polygon(12% 0, 100% 0, 100% 100%, 0 100%, 0 14%);
  }

  .brand--back {
    left: 0; right: 0; top: 56px;
    justify-content: center;
    font-size: 42px; color: var(--white);
  }
  .brand--back .brand__square { width: 18px; height: 18px; background: var(--white); }
  .rule { position: absolute; height: 1.5px; background: var(--white); }
  .rule--top { left: 70px; right: 70px; top: 126px; }
  .statement {
    position: absolute; left: 0; right: 0; top: 140px;
    text-align: center; font-size: 13.5px; font-weight: 400;
  }
  .with-line {
    position: absolute; left: 0; right: 0; top: 172px;
    display: flex; align-items: center; justify-content: center; gap: 12px;
    font-size: 13.5px;
  }
  .with-line .rule { position: static; width: 110px; }
  .benefits {
    position: absolute; left: 50px; right: 40px; top: 206px;
    list-style: none;
    display: grid; grid-template-columns: 1fr 1fr; row-gap: 12px; column-gap: 14px;
    font-size: 13.5px;
  }
  .benefits__item { display: flex; align-items: center; gap: 8px; white-space: nowrap; }
  .tick { width: 15px; height: 15px; flex: none; }
</style>
</head>
<body>

<section class="card card--front" aria-label="Business card front">
  <svg class="card__shapes" viewBox="0 0 540 310" aria-hidden="true">
    <polygon points="0,112 350,112 350,178 0,178" fill="var(--navy)"/>
    <polygon points="340,82 540,70 540,250 340,250" fill="var(--navy)"/>
    <polygon points="335,256 540,256 540,294 310,294" fill="var(--navy)"/>
    <polygon points="0,294 540,294 540,310 0,310" fill="var(--sky)"/>
    <polygon points="296,294 322,256 332,256 306,294" fill="var(--sky)"/>
  </svg>

  <div class="brand brand--front"><span class="brand__square"></span>KelpRowArc</div>

  <p class="headline">Finding &amp; Hiring Sales People Sucks!<br>Using the power of A.I. assessment tools to<br>find you the top 20% of sales talent guaranteed!</p>

  <div class="identity">
    <div class="identity__name">THOMAS MERROW</div>
    <div class="identity__role">CEO</div>
  </div>

  <div class="headshot" role="img" aria-label="Headshot of Thomas Merrow in a blazer, arms crossed"></div>

  <ul class="contact">
    <li class="contact__item">
      <svg class="contact__icon" viewBox="0 0 24 24"><path d="M6.6 10.8a15 15 0 0 0 6.6 6.6l2.2-2.2a1 1 0 0 1 1-.25 11.4 11.4 0 0 0 3.6.57 1 1 0 0 1 1 1V20a1 1 0 0 1-1 1A17 17 0 0 1 3 4a1 1 0 0 1 1-1h3.5a1 1 0 0 1 1 1c0 1.25.2 2.45.57 3.57a1 1 0 0 1-.25 1z"/></svg>
      555-318-4427
    </li>
    <li class="contact__item">
      <svg class="contact__icon" viewBox="0 0 24 24"><path d="M2 5h20v14H2z" fill="none" stroke="var(--navy)" stroke-width="2"/><path d="M2 5l10 8 10-8" fill="none" stroke="var(--navy)" stroke-width="2"/></svg>
      tmerrow@KelpRowArc.example
    </li>
    <li class="contact__item">
      <svg class="contact__icon" viewBox="0 0 24 24"><circle cx="12" cy="12" r="10" fill="none" stroke="var(--navy)" stroke-width="2"/><path d="M2 12h20M12 2c3 3 3 17 0 20M12 2c-3 3-3 17 0 20" fill="none" stroke="var(--navy)" stroke-width="1.6"/></svg>
      www.KelpRowArc.example
    </li>
    <li class="contact__item contact__item--plain">Marlow Bend, ST</li>
  </ul>
</section>

<section class="card card--back" aria-label="Business card back">
  <div class="brand brand--back"><span class="brand__square"></span>KelpRowArc</div>
  <div class="rule rule--top"></div>

  <p class="statement">The True cost of a bad hire can be as high as 10 X the first year salary</p>

  <div class="with-line"><span class="rule"></span>With KELP ROW ARC:<span class="rule"></span></div>

  <ul class="benefits">
    <li class="benefits__item"><svg class="tick" viewBox="0 0 24 24"><circle cx="12" cy="12" r="10" fill="none" stroke="#fff" stroke-width="2.4"/><path d="M7 12.5l3.2 3.2L17 9" fill="none" stroke="#fff" stroke-width="2.6"/></svg>50% Faster time to hire</li>
    <li class="benefits__item"><svg class="tick" viewBox="0 0 24 24"><circle cx="12" cy="12" r="10" fill="none" stroke="#fff" stroke-width="2.4"/><path d="M7 12.5l3.2 3.2L17 9" fill="none" stroke="#fff" stroke-width="2.6"/></svg>83% New Hire retention</li>
    <li class="benefits__item"><svg class="tick" viewBox="0 0 24 24"><circle cx="12" cy="12" r="10" fill="none" stroke="#fff" stroke-width="2.4"/><path d="M7 12.5l3.2 3.2L17 9" fill="none" stroke="#fff" stroke-width="2.6"/></svg>96% Of wrong hires eliminated</li>
    <li class="benefits__item"><svg class="tick" viewBox="0 0 24 24"><circle cx="12" cy="12" r="10" fill="none" stroke="#fff" stroke-width="2.4"/><path d="M7 12.5l3.2 3.2L17 9" fill="none" stroke="#fff" stroke-width="2.6"/></svg>50% Lower sales turnover</li>
  </ul>
</section>

</body>
</html>
```